Vosley Insurance Stationery Design Project

We need a stationery design for business cards, letterhead and envelopes.

Please refer to attached brief for further information.

Industry/Entity Type

Business

```html
<!DOCTYPE html>
<html lang="en">
<head>
<meta charset="utf-8">
<title>Vosley Insurance Business Card</title>
<link href="https://fonts.googleapis.com/css2?family=Didact+Gothic&family=Arimo:ital,wght@1,700&display=swap" rel="stylesheet">
<style>
  :root {
    --backdrop: #7a4a22;
    --card-white: #ffffff;
    --navy: #0f3550;
    --orange: #f57a22;
    --orange-deep: #ee6f17;
    --grey-brand: #bdbdbd;
    --ink: #555a5e;
    --ink-dark: #1e1e1e;
  }
  * { margin: 0; padding: 0; box-sizing: border-box; }
  html, body { width: 1200px; height: 405px; overflow: hidden; }
  body {
    background: var(--backdrop);
    font-family: "Didact Gothic", "Century Gothic", sans-serif;
    position: relative;
  }
  .card {
    position: absolute;
    top: 50px;
    width: 525px;
    height: 298px;
    border-radius: 14px;
    overflow: hidden;
  }
  .card-front { left: 45px; background: var(--card-white); }
  .card-back { left: 622px; background: var(--navy); color: #fff; }

  .accent-band {
    position: absolute;
    left: 0; right: 0; bottom: 0;
    height: 36px;
    background: linear-gradient(90deg, var(--orange-deep), var(--orange));
  }

  .brand-name {
    position: absolute;
    font-size: 38px;
    color: var(--grey-brand);
    white-space: nowrap;
    line-height: 1;
  }
  .card-front .brand-name { left: 22px; top: 86px; }
  .card-back .brand-name { left: 0; right: 0; top: 64px; text-align: center; }

  .tagline {
    position: absolute;
    left: 24px; top: 137px;
    font-family: "Arimo", Arial, sans-serif;
    font-style: italic; font-weight: 700;
    font-size: 11.5px;
    color: var(--orange);
    white-space: nowrap;
  }

  .divider {
    position: absolute;
    left: 324px; top: 39px;
    width: 1px; height: 139px;
    background: #9a9a9a;
  }

  .contact p {
    position: absolute;
    left: 343px;
    color: var(--ink);
    font-size: 13.5px;
    line-height: 16px;
    white-space: nowrap;
  }
  .contact .contact-name { color: var(--orange); font-size: 16.5px; line-height: 20px; }
  .contact .contact-role { color: var(--orange); font-size: 11.5px; }

  .web-front {
    position: absolute;
    left: 9px; bottom: 11px;
    font-size: 13px;
    color: var(--ink-dark);
  }

  .disclosure {
    position: absolute;
    left: 0; right: 0; top: 176px;
    text-align: center;
    font-size: 11px;
    line-height: 15.5px;
    white-space: nowrap;
  }
  .web-back {
    position: absolute;
    left: 0; right: 0; top: 270px;
    text-align: center;
    font-size: 13px;
  }
</style>
</head>
<body>

<section class="card card-front" aria-label="Business card front">
  <div class="accent-band" role="img" aria-label="Orange accent band along the lower edge of the card"></div>

  <p class="brand-name">Vosley Insurance</p>
  <p class="tagline">Business and Life Insurance Brokers and Advisers</p>

  <div class="divider"></div>

  <div class="contact">
    <p class="contact-name" style="top:38px">Mark Holloway</p>
    <p class="contact-role" style="top:60px">Director</p>
    <p style="top:93px">Level 4, 18 Harbour Lane</p>
    <p style="top:109px">Eastbrook NSW 2071</p>
    <p style="top:132px">PO Box 412.</p>
    <p style="top:149px">Eastbrook NSW 2070</p>
    <p style="top:175px">T : (02) 5550 1284</p>
    <p style="top:197px">M : 0400 555 219</p>
    <p style="top:216px">F : (02) 5550 1290</p>
    <p style="top:235px">E : mholloway@vosley.net.au</p>
  </div>

  <p class="web-front">www.vosleyinsurance.com.au</p>
</section>

<section class="card card-back" aria-label="Business card back">
  <p class="brand-name">Vosley Insurance</p>
  <div class="disclosure">
    <p>Authorised Representative No. 408213</p>
    <p>Harlow Cover Network Pty Limited AFSL 251730 Insurance</p>
    <p>Harlow Financial Services Pty Ltd and its advisers are members of Ardent</p>
    <p>Financial Advisers and Authorised Representatives of Kestrel Advice Group Pty Ltd AFSL 263914</p>
  </div>
  <p class="web-back">www.vosleyinsurance.com.au</p>
</section>

</body>
</html>
```